Design my site www.brieflyledger.com

So here is what I am thinking in terms of design:

https://plenvo.com

https://www.skyluxair.com

http://kalvex.com/harbor-plaza-tower/

I want the theme to be white and blue (royal blue). I attached a paint picture of what I would like the site to look like in terms of placing the text. Generally, what I like about the sites above is that they are simple, you can navigate easily and have some kind of idea of what's going on by looking at the center (picture and motto). Let's establish a clear understanding of how the functional part of the site would look like. Please see the picture attached.

I want to keep it simple: On top would be the Name 'BRIEFLY ledger", somewhere to the right on top on the page would be 'Sign in" button.

In the center would be a picture (maybe a video) with the Motto (on top of it all in capital) OBSERVE NAVIGATE DECIDE and below would be the "sign up now"

Below the picture (like on kalvex.com site) or to the left on top of the page would be "About Us', "Press" "Contact Us' buttons.

Then once the user gets to his page his got 3 tabs " Press Headlines", "Events", " Briefings".

we would keep the same format I only have on the site, but separate for every Tab.

I do not want the user to get distracted. I also want him to be able to access the page though mobile phone and be able to get automatic updates just like Zorvan Pings without having to sign in daily.

The landing page must be minimalist yet with business/corporate feel where users can navigate easily and a "what you see is what you get" approach. You want an image or video (personally I prefer the video.. it does capture the users attention instantly, as long as it is an interesting video), with your taglines in it.

Sections available to public: About Us, Contact Us, Landing Page with Signup Option

Private: Public Sections + User Account Page, Tabs for (Events, Press Headlines, Briefings)

Target Market(s)

PR/media monitoring/diplomatic community

Coding

Coded - Design and coding required

Number of Pages Required

1 page

Font styles to use
Serif
Sans Serif

Colors
0255a3
ec1f27

Requirements
Must have
• a simple landing page, that is user friendly.
Nice to have
• a video with the explanation of how to navigate the site
Should not have
• too many colors, graphs etc.

```html
<!DOCTYPE html>
<html lang="en">
<head>
<meta charset="utf-8">
<title>BRIEFLY LEDGER</title>
<link rel="stylesheet" href="https://fonts.googleapis.com/css2?family=Open+Sans:wght@400;600&display=swap">
<style>
  :root {
    --royal: #0255a3;
    --royal-deep: #034a92;
    --royal-light: #1c68b4;
    --alert: #ec1f27;
    --white: #ffffff;
    --body-text: #666666;
    --arrow: #e6e6e6;
    --footer-top: #4a4a4a;
    --footer-bottom: #333333;
    --sky-top: #8fa9b8;
    --sky-mid: #c9d4d6;
    --city: #7e97a4;
  }
  * { box-sizing: border-box; margin: 0; padding: 0; }
  html, body { width: 1200px; height: 657px; overflow: hidden; }
  body {
    position: relative;
    font-family: "Open Sans", Arial, sans-serif;
    background: var(--sky-mid);
  }
  .hero-backdrop {
    position: absolute; inset: 0 0 50px 0;
    background:
      linear-gradient(90deg, rgba(60,80,95,.35) 0%, rgba(60,80,95,.15) 38%, rgba(255,255,255,0) 45%),
      linear-gradient(180deg, var(--sky-top) 0%, var(--sky-mid) 40%, #c5d2d6 65%, var(--city) 100%);
  }
  .site-title {
    position: absolute; left: 97px; top: 50px;
    font-family: Arial, "Helvetica Neue", sans-serif;
    font-weight: 700; font-size: 31px; letter-spacing: .2px;
    color: var(--white);
  }
  .sign-in {
    position: absolute; left: 1016px; top: 50px; width: 86px; height: 37px;
    display: flex; align-items: center; justify-content: center;
    background: linear-gradient(180deg, var(--royal-light), var(--royal-deep));
    border-radius: 3px; color: var(--white);
    font-family: Arial, sans-serif; font-size: 16px; text-decoration: none;
  }
  .dashboard {
    position: absolute; left: 150px; top: 147px; width: 899px; height: 377px;
    background: var(--white);
    box-shadow: 0 2px 6px rgba(0,0,0,.3);
  }
  .tabs { display: flex; height: 49px; }
  .tab {
    flex: 1; display: flex; align-items: center; justify-content: center;
    background: var(--royal); color: var(--white);
    font-family: Arial, sans-serif; font-size: 21px;
  }
  .tab + .tab { border-left: 1px solid #1d74d0; }
  .tab.is-active { background: var(--alert); border-left: none; }
  .step {
    position: absolute; top: 105px; width: 258px; text-align: center;
  }
  .step-icon {
    width: 125px; height: 109px; margin: 0 auto;
    background: linear-gradient(180deg, var(--royal-light), var(--royal-deep));
    border-radius: 3px; box-shadow: 0 1px 3px rgba(0,0,0,.3);
    display: flex; align-items: center; justify-content: center;
  }
  .step-title {
    margin-top: 17px; font-size: 17px; font-weight: 600; color: var(--royal);
  }
  .step-text {
    margin-top: 3px; font-size: 12px; line-height: 19.7px; color: var(--body-text);
    text-align: justify; text-align-last: center;
  }
  .flow-arrow { position: absolute; top: 149px; width: 107px; height: 41px; }
  .site-footer {
    position: absolute; left: 0; bottom: 0; width: 1200px; height: 50px;
    background: linear-gradient(180deg, var(--footer-top), var(--footer-bottom));
    color: var(--white); font-size: 12px;
  }
  .copyright { position: absolute; left: 104px; top: 17px; }
  .footer-links { position: absolute; left: 969px; top: 17px; display: flex; gap: 19px; }
  .footer-links a { color: var(--white); text-decoration: none; }
</style>
</head>
<body>
  <div class="hero-backdrop" role="img" aria-label="Photo of glass office tower and city skyline with bridge under a pale sky"></div>

  <header>
    <h1 class="site-title">BRIEFLY LEDGER</h1>
    <a class="sign-in" href="#">SIGN IN</a>
  </header>

  <main class="dashboard">
    <nav class="tabs">
      <div class="tab">PRESS HEADLINES</div>
      <div class="tab">EVENTS</div>
      <div class="tab is-active">BRIEFINGS</div>
    </nav>

    <section class="step" style="left:28px">
      <div class="step-icon">
        <svg width="42" height="46" viewBox="0 0 42 46"><circle cx="21" cy="11" r="11" fill="#fff"/><path d="M0 44 Q0 25 12 24 L30 24 Q42 25 42 44 Q42 46 40 46 L2 46 Q0 46 0 44Z" fill="#fff"/></svg>
      </div>
      <h2 class="step-title">LOG IN</h2>
      <p class="step-text">Lorem Ipsum is simply dummy text of the printing and typesetting industry. Lorem Ipsum has been the industry's standard dummy text ever since the 1500s,</p>
    </section>

    <svg class="flow-arrow" style="left:249px" viewBox="0 0 107 41"><path d="M4 36 Q40 -2 80 18" fill="none" stroke="var(--arrow)" stroke-width="9"/><path d="M70 4 L107 41 L62 41Z" fill="var(--arrow)"/></svg>

    <section class="step" style="left:320px">
      <div class="step-icon">
        <svg width="42" height="46" viewBox="0 0 42 46"><circle cx="21" cy="11" r="11" fill="#fff"/><path d="M0 44 Q0 25 12 24 L30 24 Q42 25 42 44 Q42 46 40 46 L2 46 Q0 46 0 44Z" fill="#fff"/></svg>
      </div>
      <h2 class="step-title">KEY WORDS</h2>
      <p class="step-text">Lorem Ipsum is simply dummy text of the printing and typesetting industry. Lorem Ipsum has been the industry's standard dummy text ever since the 1500s,</p>
    </section>

    <svg class="flow-arrow" style="left:542px" viewBox="0 0 107 41"><path d="M4 36 Q40 -2 80 18" fill="none" stroke="var(--arrow)" stroke-width="9"/><path d="M70 4 L107 41 L62 41Z" fill="var(--arrow)"/></svg>

    <section class="step" style="left:611px">
      <div class="step-icon">
        <svg width="42" height="46" viewBox="0 0 42 46"><circle cx="21" cy="11" r="11" fill="#fff"/><path d="M0 44 Q0 25 12 24 L30 24 Q42 25 42 44 Q42 46 40 46 L2 46 Q0 46 0 44Z" fill="#fff"/></svg>
      </div>
      <h2 class="step-title">DATE RANGE</h2>
      <p class="step-text">Lorem Ipsum is simply dummy text of the printing and typesetting industry. Lorem Ipsum has been the industry's standard dummy text ever since the 1500s,</p>
    </section>
  </main>

  <footer class="site-footer">
    <p class="copyright">Copyright © 2016 BRIEFLY ledger</p>
    <nav class="footer-links"><a href="#">Terms of Use</a><a href="#">Privacy</a></nav>
  </footer>
</body>
</html>
```